Yoga/movement guide/teacher for adult yoga practice and kid yoga

What is the positioning or mission statement of your company? to guide individuals in a yoga-based safe and sustainable movement practice applicable to all ages and body types. Currently my focus is working with children in daycare and school settings, but my goal is to expand into private yoga practice for adults, and potentially as part of rented space in studios. I hope to find a way to work with children AND adults (so would love for logo to be appealing to both), but current focus is with children based on need and demand in the community. yoga for children also compliments my backround as a pediatrician/neonatologist, and I greatly miss interacting with children. I also want to emphasize a yoga/movement practice that is focused more on what one feels internally through movement. NOT what one looks like asthetically. I believe in removing all mirrors from yoga/movement practice. It should be an experience of movement/poses/yoga through appropriate cueing and education. It is not about the details of how far the knee should bend, or how high the leg should be. Focusing on foudation first, core, then core engagement and ultimately expression of poses/movements. A focus on strength, stability and mobility, not just flexibility, which is the common perception/association with yoga. I also want individuals to learn to be an advocate of their own health. Through guidance, I hope for individuals to connect with their body so they know themselves so well to be able to advocate for themselves in the modern healthcare world. This internal experience and connection is so essential in a world where modern medicine has become a business and it is all about making a dollar. the connection with patients is lost, and individuals need to learn to empower themselves and through their new found voice to be able to articulate what is wrong.<br/>Does your company have a tagline or slogan that should be included with the logo? "Move With Inner Light"<br/>What do you hope your company can be known for? Accessible yoga for a sustained practice. A guided movement practice where one gains information and knowledge of oneself through a mind/body connection. For one feel good physically with a new awaraness of their internal radiance that exists in all beings. Physical rejuvenation egnites a light and increases energy to flow through the physical body, which ultimately tranlates into works of kindness for others and out in the world. <br/>What color palettes might you prefer? why? love the colors currently chosen<br/>Where will the logo be primarily used? initially business cards, but hopefully future websites, t-shirts, and potentially local magazine adds. Also starting with a small couple of banners for community events in the area. I currently practice as a nomad out of my car :)<br/>Are there any elements you would prefer to see in the logo? Movement. A modern depiction of a human body/figure practicing movement. Hoping to avoid a stereotypical yoga pose per say, just because I want to people to think of it more of a movement practice with yoga roots. Modern yoga. There are elements of breathing and connecting with oneself through the flow of breath and movement, but I do not focus on the meditative/cerebral aspect of the yoga practice. What I teach is almost reaching a meditative state through movement. I personally don't practice, nor resonate with just seated meditation. just not my thing :)<br/>In your opinion, what defines a well-designed logo? curiosity. enough info for individuals to think they know what it means, but want to know more. invokes curiosity, but not too abstract. Reproducible. not too complicated. I want also to invoke a community feel, so a design that appeals to all people within a community. <br/>What is your preference in reference to icons, typography, spokespeople (characters), etc.? modern design. I love the idea of a logo for my purposes, to invoke a sense of movement from within. So not too static. <br/>What words or icons must be included in the logo? movement with yoga roots. <br/>What logos do you like and why? A representation, but not exact. I think some ambiguity is intriguing for others, and also memorable. I want it to be an artistic representation of movement/yoga<br/>What logos do you dislike and why? too busy, too loud. <br/>In your opinion, what is the primary purpose for a logo? association<br/>Who is the primary target audience? (who is most likely to use your services/product?) Children and their parents, but ultimately to expand into teaching adults. I even have aspirations of prenatal and post-natal yoga. Potentially incorporating infants. <br/>Who currently uses your product the most? n/a (working in schools/daycare currently. It is currently all volunteer)<br/>Are you pleased with the range of people your company serves? n/a<br/>Are you looking to expand, modify, or completely change your target audience? or will it remain the same? yes! expand into an adult audience. <br/>How do you plan to focus on your target audience? currently by working through schools and daycares. hopefully ultimately through after school care programs and then offering kid yoga in an existing yoga studio (working on this with Q Studio in Ridgeland, currently)<br/>What are your main forms of advertising? word of mouth, schools, daycares. Happy kids talking to their parents about the yoga class they took and happy teachers :)<br/>How do most customers find out about your company?<br/>Which gender are you targeting? All genders! However, with kid yoga, often the maternal individual in the child's life is more involved with decision making as far as extracurricular activities

Target Market(s)

individuals and families interested in wellness and feeling great

Contact Information for Business Card

Dana Whitford
Yoga Instructor
RYT-200, RCYT

certified yoga teacher for adults and children

Colors

Designer to choose colors to be used in the design.

Requirements
Must have
• "Move With Inner Light"
Nice to have
• logo with same colors

```html
<!DOCTYPE html>
<html lang="en">
<head>
<meta charset="utf-8">
<title>Brightwell Studios – Business Card</title>
<link rel="stylesheet" href="https://fonts.googleapis.com/css2?family=Arimo:wght@400&family=Indie+Flower&display=swap">
<style>
  :root {
    --backdrop: #1e1e1e;
    --card-white: #ffffff;
    --card-grey: #808281;
    --sun-yellow: #f4dc3c;
    --sky-teal: #5ec9d1;
    --ink-grey: #5a5a5a;
  }
  * { margin: 0; padding: 0; box-sizing: border-box; }
  html, body {
    width: 1200px; height: 900px; overflow: hidden;
    background: var(--backdrop);
    font-family: "Arimo", Arial, sans-serif;
  }
  .sheet {
    width: 1200px; height: 900px;
    display: flex; flex-direction: column; align-items: center; justify-content: center;
    gap: 40px;
  }
  .card { position: relative; width: 700px; height: 400px; overflow: hidden; flex: none; }

  /* back face */
  .card--back { background: var(--card-grey); }
  .card--back .brand-lockup {
    position: absolute; left: 50%; top: 50%; transform: translate(-50%, -50%);
    display: flex; align-items: center; gap: 18px;
  }
  .brand-dot {
    flex: none; width: 90px; height: 90px; border-radius: 50%; background: var(--sun-yellow);
  }
  .brand-name { white-space: nowrap; line-height: 1.1; }
  .card--back .brand-name { font-size: 34px; color: var(--sun-yellow); }

  /* front face */
  .card--front { background: var(--card-white); }
  .sun-panel { position: absolute; inset: 0; }
  .contact { position: absolute; left: 80px; top: 120px; }
  .contact__name {
    font-family: "Indie Flower", cursive; font-weight: 400;
    font-size: 38px; color: var(--sun-yellow); line-height: 1; white-space: nowrap;
  }
  .contact__role { font-size: 19px; color: var(--ink-grey); margin-top: 2px; }
  .contact__list { list-style: none; margin-top: 26px; }
  .contact__item {
    display: flex; align-items: center; gap: 10px; white-space: nowrap;
    font-size: 19px; color: var(--ink-grey); line-height: 27px;
  }
  .contact__item svg { width: 18px; height: 18px; flex: none; }
  .card--front .brand-lockup {
    position: absolute; left: 470px; top: 120px; width: 220px;
    display: flex; flex-direction: column; align-items: center; text-align: center;
  }
  .card--front .brand-dot { background: var(--card-white); width: 110px; height: 110px; }
  .card--front .brand-name { margin-top: 16px; font-size: 26px; color: var(--ink-grey); }
  .tagline {
    margin-top: 10px; font-size: 10px; letter-spacing: 2px; text-transform: uppercase;
    color: var(--sky-teal); white-space: nowrap;
  }
</style>
</head>
<body>
<main class="sheet">
  <section class="card card--back" aria-label="Card back">
    <div class="brand-lockup">
      <span class="brand-dot"></span>
      <span class="brand-name">Brightwell Studios</span>
    </div>
  </section>

  <section class="card card--front" aria-label="Card front">
    <svg class="sun-panel" viewBox="0 0 700 400" aria-hidden="true">
      <circle cx="760" cy="200" r="370" fill="var(--sun-yellow)"/>
      <path d="M 470 20 Q 340 200 450 385" fill="none" stroke="var(--card-white)" stroke-width="7" stroke-linecap="round"/>
    </svg>

    <div class="contact">
      <h1 class="contact__name">Dana Whitford</h1>
      <p class="contact__role">Owner-Operator</p>
      <ul class="contact__list">
        <li class="contact__item">
          <svg viewBox="0 0 20 20"><circle cx="10" cy="10" r="8.5" fill="none" stroke="var(--sky-teal)" stroke-width="1.5"/><path d="M7 6c-.6 2 1.6 6.2 5 7.2l1.2-1.4-1.8-1.2-.9.8c-1-.5-2-1.6-2.4-2.6l.8-.9-1-1.9z" fill="var(--sky-teal)"/></svg>
          601-555-0147
        </li>
        <li class="contact__item">
          <svg viewBox="0 0 20 20"><rect x="2" y="5" width="16" height="11" fill="none" stroke="var(--sky-teal)" stroke-width="1.5"/><path d="M2 5l8 6 8-6" fill="none" stroke="var(--sky-teal)" stroke-width="1.5"/></svg>
          danawhitford@mailbox.com
        </li>
        <li class="contact__item">
          <svg viewBox="0 0 20 20"><circle cx="10" cy="10" r="8" fill="none" stroke="var(--sky-teal)" stroke-width="1.5"/><ellipse cx="10" cy="10" rx="3.5" ry="8" fill="none" stroke="var(--sky-teal)" stroke-width="1.2"/><path d="M2 10h16M3.5 6h13M3.5 14h13" stroke="var(--sky-teal)" stroke-width="1.2"/></svg>
          www.brightwellstudios.com
        </li>
      </ul>
    </div>

    <div class="brand-lockup">
      <span class="brand-dot"></span>
      <span class="brand-name">Brightwell Studios</span>
      <p class="tagline">Move With Inner Light</p>
    </div>
  </section>
</main>
</body>
</html>
```